Brochure for a civil enineering company in A4 format

I need a brochure design for our company TIRO Engineering S.r.l.. We are an engineering consultant company. Our main clients are from the infrastructure industry (geotechnical and underground sectors mainly).
We are looking for a 2 pages (4 faces) fold out design with a glued pocket where we can put individual data sheets.
I need A4 format pages.

Target Market(s)

We are an engineering consultant company. Our main clients are from the infrastructure industry (geotechnical and underground sectors mainly).

Industry/Entity Type

Civil Engineer

Font styles to use
Sans Serif

Requirements
Must have
• Overall: 2 pages in A4 format
Essential style. Bright and modern appearance.
Glued pocket
Logo integrated in a picture on the pocket where I would like to insert a slogan (… tiro engineering … reliable solutions …)
Attached are selected images which the designer can use and edit at their own discretion.
Some advice in the following (anyway designers are free to provide their solutions):
Outer sheets:
Front page with name, logo. It could be nice to have the “m” of the logo integrated in a pictures, also a modified picture (I mean modify one of the attached pictures) so to create a general image and do not tie the cover to a specific job.
Back page: offices address and contact email address. Nice to have one space for a slogan.
Inner sheet: text that I upload in the file “inside-sheets”, possibly with pictures on each sheet. In the right faces insert the glued pocket. On this pages insert the section OUR EXPERIENCE ….with a space for a picture of our team.
Nice to have
• Clean and essential design.
Pictures choosing from the atteched ones. Pictures could be modified in a very light manner to make them a general idea of the work ( I mean geotechnical world) without to be immediately linked to a specific site.
Should not have
• excessive frills

```html
<!DOCTYPE html>
<html lang="it">
<head>
<meta charset="utf-8">
<title>TIRO Engineering – Brochure</title>
<link rel="stylesheet" href="https://fonts.googleapis.com/css2?family=Fira+Sans:ital,wght@0,400;0,600;0,700;0,800;1,400;1,600;1,700&display=swap">
<style>
  :root {
    --bg: #d9d6da;
    --paper: #ffffff;
    --paper-shade: #f1f1f2;
    --navy: #2b3468;
    --ink: #1e1e24;
    --accent: #a3163f;
    --photo-blue: #3a4479;
    --photo-dark: #1b1f40;
  }
  * { margin: 0; padding: 0; box-sizing: border-box; }
  html, body { width: 1200px; height: 675px; overflow: hidden; }
  body {
    background: var(--bg);
    font-family: "Fira Sans", sans-serif;
    color: var(--ink);
    position: relative;
  }
  .brochure {
    position: absolute;
    left: 51px; top: 78px;
    width: 1098px; height: 518px;
    display: flex;
    box-shadow: 0 6px 24px rgba(0,0,0,.12);
  }
  .panel { position: relative; width: 366px; height: 518px; background: var(--paper); overflow: hidden; }

  /* Services panel */
  .panel--services .backdrop {
    position: absolute; inset: 0 0 22px 0;
    background: linear-gradient(160deg, #6a72a0 0%, var(--photo-blue) 40%, var(--photo-dark) 100%);
  }
  .services-column {
    position: absolute; left: 18px; top: 0; width: 222px; height: 370px;
    background: var(--paper); padding: 16px 14px 0 14px;
  }
  .services-title {
    font-weight: 800; font-size: 31px; line-height: .92; color: var(--navy);
    letter-spacing: .5px; padding-bottom: 6px; border-bottom: 1.5px solid var(--ink);
  }
  .services-lead { font-weight: 700; font-style: italic; font-size: 7.4px; line-height: 1.25; margin: 8px 0 6px; }
  .services-body p { font-size: 5.6px; line-height: 1.32; margin-bottom: 5px; }
  .services-list { list-style: none; }
  .services-list li { font-size: 5.6px; line-height: 1.32; font-style: italic; color: var(--accent); margin-bottom: 5px; }
  .inset-photo {
    position: absolute; left: 18px; top: 370px; width: 168px; height: 126px;
    background: linear-gradient(135deg, #5b5148 0%, #8a6b4a 45%, #c56a2a 60%, #3c3a3c 100%);
  }

  /* Offices panel */
  .panel--offices { background: linear-gradient(90deg, var(--paper) 0%, var(--paper-shade) 100%); }
  .offices { position: absolute; left: 108px; top: 376px; font-style: normal; font-size: 7.4px; line-height: 1.32; }
  .offices-title { font-weight: 700; font-size: 12.5px; color: var(--navy); margin-bottom: 2px; }
  .office { margin-bottom: 6px; }
  .office-city { font-weight: 700; }
  .web { font-weight: 700; }

  /* Pocket / cover panel */
  .panel--cover { background: linear-gradient(90deg, var(--paper-shade) 0%, var(--paper) 40%); }
  .cover-photo {
    position: absolute; left: 34px; top: 30px; width: 216px; height: 400px;
    background: radial-gradient(circle at 42% 48%, #f4f4f6 0%, #b9bdcf 14%, #5c6596 38%, var(--photo-blue) 60%, var(--photo-dark) 100%);
  }
  .brand { position: absolute; left: 34px; top: 446px; }
  .brand-name { font-weight: 700; font-size: 40px; line-height: 1; color: var(--ink); letter-spacing: .5px; }
  .brand-slogan { font-weight: 400; font-size: 7.5px; color: var(--ink); margin-top: 4px; }
</style>
</head>
<body>
  <main class="brochure">
    <section class="panel panel--services">
      <div class="backdrop" role="img" aria-label="Foto di galleria in costruzione con pala gommata, toni blu"></div>
      <div class="services-column">
        <h1 class="services-title">OUR<br>SERVICES</h1>
        <p class="services-lead">Progettazione e consulenza specialistica nel campo della geologia, dell'ingegneria geotecnica, delle opere sotterranee e dell'ingegneria idraulica.</p>
        <div class="services-body">
          <p>Aiutiamo i nostri clienti a risolvere problemi di natura progettuale, contrattuale e costruttiva che possono nascere nell'intera vita del progetto portando la nostra esperienza all'interno delle loro organizzazioni, migliorando la qualità dei loro servizi di ingegneria, ottimizzando i loro progetti, proponendo nuove idee e soluzioni, rafforzando i loro approcci.</p>
          <p>TIRO Engineering è in grado di fornire la propria assistenza nell'intero iter procedurale, dalla fase di indagine preliminare e di analisi di fattibilità fino alla progettazione costruttiva e all'assistenza tecnica in fase realizzativa.</p>
          <p>La specializzazione e l'esperienza accumulate nelle discipline della geologia, dell'ingegneria geotecnica e del sottosuolo e dell'idraulica ci permette di massimizzare la nostra efficacia quando sia necessario:</p>
        </div>
        <ul class="services-list">
          <li>• far fronte a situazioni di emergenza anche su progetti in fase di sviluppo avanzato garantendo l'immediata focalizzazione delle problematiche di progetto e garantendo il risultato finale atteso (in termini di qualità, tempistiche e costi...)</li>
          <li>• fornire "second opinion" di elevato valore tecnico ed amministrativo in occasione di problematiche progettuali e costruttive e dispute legali</li>
          <li>• analizzare in tempi brevi progetti svolti da terzi individuandone le "criticità", verificandone la cantierabilità e la validità tecnico economica.</li>
          <li>• ottimizzare i progetti redatti da terzi implementandone il contenuto e massimizzando l'efficacia economica degli investimenti.</li>
        </ul>
      </div>
      <div class="inset-photo" role="img" aria-label="Foto di escavatori al fronte di scavo in galleria"></div>
    </section>

    <section class="panel panel--offices">
      <address class="offices">
        <h2 class="offices-title">OUR OFFICES</h2>
        <div class="office">
          <div class="office-city">Milano</div>
          Via Verdi, 14<br>20121 Milano - IT<br>T: +39 02 555018844<br>E: info@tiroengineering.example
        </div>
        <div class="office">
          <div class="office-city">Arco TN</div>
          Via S. MARCO, 9<br>38062 Arco TN - IT<br>T: +39 02 555018844<br>E: info@tiroengineering.example
        </div>
        <div class="web">Web: www.tiroengineering.example</div>
      </address>
    </section>

    <section class="panel panel--cover">
      <div class="cover-photo" role="img" aria-label="Foto di galleria con centine e luce in fondo, toni blu"></div>
      <div class="brand">
        <div class="brand-name">tiro</div>
        <p class="brand-slogan">Consulenza geotecnica e opere in sotterraneo</p>
      </div>
    </section>
  </main>
</body>
</html>
```